Velundra Jobs portal

Velundra Jobs is a job portal connecting job seekers and companies offering part time jobs in the Mena region, starting in the UAE. We would like to see designs that use the color blue. We have attached images to give an idea what the website should look like. When a company posts a job the job seekers are not allowed to see which company has posted a job. There should also be a coinvex gateway. On the landing page we want a catching picture that we will send.

Target Market(s)

Students and promotional workers

Logo Text

Velundra Jobs

Coding

Coded - Design and coding required

Number of Pages Required

4 page

Font styles to use
Sans Serif

Colors
33a6d7
0692cd
85cae6

```html
<!DOCTYPE html>
<html lang="en">
<head>
<meta charset="utf-8">
<title>Velundra Jobs – Job Seeker</title>
<link href="https://fonts.googleapis.com/css2?family=Roboto:wght@300;400;500&family=Open+Sans:wght@400;600&display=swap" rel="stylesheet">
<style>
:root{
  --blue:#33a6d7;
  --blue-dark:#0692cd;
  --blue-light:#85cae6;
  --row-a:#dceef7;
  --row-b:#eef7fb;
  --ink:#555;
  --ink-soft:#777;
  --link:#1a8ac4;
  --panel:#f2f2f2;
  --footer:#333333;
  --footer-text:#c9c9c9;
  --badge:#8e3a96;
}
*{box-sizing:border-box;margin:0;padding:0}
html,body{width:1094px;height:1200px;overflow:hidden}
body{font-family:"Roboto",Arial,sans-serif;background:#fff;color:var(--ink);position:relative}
.top-stripe{height:4px;background:linear-gradient(90deg,#3b9ad8,#7a6fc8,#d46aa0)}
.site-header{height:93px;background:linear-gradient(#fff,#f6f6f6);position:relative}
.brand{position:absolute;left:90px;top:18px;display:flex;align-items:center;gap:10px}
.brand-mascot{width:50px;height:62px;border-radius:8px;background:linear-gradient(135deg,#3fa9d9,#b25aa8)}
.brand-name{font-size:30px;font-weight:300;color:var(--blue)}
.main-nav{position:absolute;left:609px;top:43px;font-size:13px;color:#999}
.main-nav a{text-decoration:none;color:#999}
.main-nav a.active{color:#2c6fa6}
.main-nav .sep{margin:0 8px;color:#bbb}
.icon-search{position:absolute;left:770px;top:42px}
.icon-bell{position:absolute;left:820px;top:38px}
.badge{position:absolute;left:832px;top:33px;width:17px;height:17px;border-radius:50%;background:var(--badge);color:#fff;font-size:8px;text-align:center;line-height:17px}
.avatar{position:absolute;left:877px;top:22px;width:55px;height:55px;border-radius:50%;background:linear-gradient(#c9b3a0,#8a6d5a);border:3px solid #e8e8e8}
.logout{position:absolute;left:948px;top:37px;width:55px;height:25px;border:1px solid #ccc;border-radius:2px;font-size:9px;color:#888;text-align:center;line-height:23px;background:#fff}

.search-band{height:73px;background:var(--blue);display:flex;align-items:center;padding-left:91px;gap:12px}
.search-band h1{font-size:21px;font-weight:400;color:#fff;letter-spacing:.5px;width:135px}
.filter{height:32px;background:#fff;border-radius:2px;font-size:10.5px;color:#666;display:flex;align-items:center;justify-content:space-between;padding:0 13px;width:160px}
.filter .caret{width:0;height:0;border-left:5px solid transparent;border-right:5px solid transparent;border-top:6px solid #999}
.filter.wide{width:218px}
.search-btn{width:32px;height:32px;background:var(--blue-light);border-radius:2px;display:flex;align-items:center;justify-content:center}

.content{position:absolute;top:170px;left:0;width:1094px;height:699px}
.categories{position:absolute;left:90px;top:0;width:193px;height:672px;background:var(--panel);list-style:none;padding:18px 0 0 18px}
.categories li{height:38.2px;font-size:12px;color:#666}
.jobs{position:absolute;left:306px;top:26px;width:696px;border-collapse:collapse;font-size:11px}
.jobs th{background:var(--blue-dark);color:#fff;font-weight:400;height:37px;text-align:left;font-size:11.5px;border-right:1px solid #3aa8dc}
.jobs th:last-child{border-right:0}
.jobs td{height:46.9px;border-right:1px solid #fff;border-bottom:1px solid #fff;color:#666}
.jobs td:last-child{border-right:0;text-align:right;padding-right:8px}
.jobs tr:nth-child(odd) td{background:var(--row-a)}
.jobs tr:nth-child(even) td{background:var(--row-b)}
.col-title{width:168px;padding-left:24px}
.col-date{width:172px;padding-left:51px}
.col-provider{width:218px;padding-left:66px}
.jobs td.col-title a{color:var(--link);text-decoration:none}
.apply{display:inline-block;width:65px;height:26px;border:1px solid #d6d6d6;background:#fff;font-size:9px;color:#999;text-align:center;line-height:24px;border-radius:2px}

.providers{position:absolute;top:869px;left:0;width:1094px;height:109px;background:var(--panel)}
.providers h2{position:absolute;left:90px;top:32px;font-size:12.5px;font-weight:400;color:#555}
.carousel-arrows{position:absolute;left:975px;top:32px;display:flex;gap:10px}
.provider-list{position:absolute;left:92px;top:63px;width:910px;display:flex;justify-content:space-between;align-items:center;list-style:none}
.provider-list li{font-size:15px;font-weight:500;color:#666}

.site-footer{position:absolute;top:978px;left:0;width:1094px;height:222px;background:var(--footer);font-family:"Open Sans",Arial,sans-serif;color:var(--footer-text)}
.footer-col{position:absolute;top:28px}
.footer-col h3{font-size:11px;font-weight:400;color:#fff;margin-bottom:10px}
.footer-col ul{list-style:none;font-size:9.5px;line-height:18.7px}
.footer-col li::before{content:"•";margin-right:6px;color:#999}
.cols2{display:flex;gap:50px}
.divider{position:absolute;top:24px;width:1px;height:105px;background:#4a4a4a}
.newsletter-field{display:flex;width:143px;height:25px;margin-top:-2px}
.newsletter-field span{flex:1;background:#fff;font-size:9.5px;color:#888;padding:6px 9px}
.newsletter-field b{width:31px;background:#ddd;display:flex;align-items:center;justify-content:center}
.social{display:flex;gap:7px;margin-top:14px}
.social i{width:25px;height:25px;border-radius:50%;display:block}
.rule{position:absolute;left:93px;top:154px;width:906px;height:1px;background:#4d4d4d}
.copyright{position:absolute;left:90px;top:182px;font-size:9px;color:#ddd}
.footer-icons{position:absolute;left:945px;top:174px;display:flex;gap:8px}
</style>
</head>
<body>
<div class="top-stripe"></div>
<header class="site-header">
  <div class="brand">
    <div class="brand-mascot" role="img" aria-label="Velundra Jobs mascot illustration"></div>
    <span class="brand-name">Velundra Jobs</span>
  </div>
  <nav class="main-nav"><a class="active" href="#">About us</a><span class="sep">|</span><a href="#">Contact us</a></nav>
  <svg class="icon-search" width="24" height="24" viewBox="0 0 24 24"><circle cx="10" cy="10" r="7" fill="none" stroke="#888" stroke-width="3"/><line x1="15" y1="15" x2="21" y2="21" stroke="#888" stroke-width="3.5" stroke-linecap="round"/></svg>
  <svg class="icon-bell" width="26" height="28" viewBox="0 0 26 28"><path d="M5 20 Q6 17 6 12 Q6 5 13 5 Q20 5 20 12 Q20 17 21 20 Z" fill="none" stroke="#999" stroke-width="1.6"/><path d="M10 22 Q13 25 16 22" fill="none" stroke="#999" stroke-width="1.6"/></svg>
  <span class="badge">23</span>
  <div class="avatar" role="img" aria-label="Signed-in user profile photo"></div>
  <div class="logout">Log out</div>
</header>

<section class="search-band">
  <h1>JOB SEEKER</h1>
  <div class="filter">Job Type<span class="caret"></span></div>
  <div class="filter">Salary<span class="caret"></span></div>
  <div class="filter">Location<span class="caret"></span></div>
  <div class="filter wide">Languages Spoken :</div>
  <div class="search-btn"><svg width="14" height="14" viewBox="0 0 14 14"><circle cx="6" cy="6" r="4.3" fill="none" stroke="#1b6f97" stroke-width="1.8"/><line x1="9.2" y1="9.2" x2="12.5" y2="12.5" stroke="#1b6f97" stroke-width="2" stroke-linecap="round"/></svg></div>
</section>

<main class="content">
  <ul class="categories">
    <li>Aliquam vitae sapien&nbsp; (33)</li>
    <li>Nulla ut neque&nbsp; (3)</li>
    <li>Nam ultrices orci&nbsp; (23)</li>
    <li>Proin ut enim&nbsp; (13)</li>
    <li>Donec aliquam quam&nbsp; (42)</li>
    <li>In pulvinar nibh&nbsp; (18)</li>
    <li>Nunc pellentesque&nbsp; (31)</li>
    <li>Aliquam dignissim&nbsp; (189)</li>
    <li>Tellus scelerisque&nbsp; (54)</li>
    <li>Nulla porttitor&nbsp; (64)</li>
    <li>Nam tempus&nbsp; (48)</li>
    <li>Vestibulum non&nbsp; (57)</li>
    <li>Ut vel mauris ultricies&nbsp; (77)</li>
    <li>Duis hendrerit&nbsp; (23)</li>
    <li>Pellentesque&nbsp; (35)</li>
    <li>Posuere diam et&nbsp; (58)</li>
    <li>Nam elementum&nbsp; (64)</li>
  </ul>

  <table class="jobs">
    <thead><tr><th class="col-title">Job Title</th><th class="col-date">Due Date</th><th class="col-provider">Provider Name</th><th></th></tr></thead>
    <tbody>
      <tr><td class="col-title"><a href="#">Maecenas sed nibh</a></td><td class="col-date">Apr 8, 2015</td><td class="col-provider">Company Name</td><td><span class="apply">Apply Now</span></td></tr>
      <tr><td class="col-title"><a href="#">Maecenas sed nibh</a></td><td class="col-date">Apr 8, 2015</td><td class="col-provider">Company Name</td><td><span class="apply">Apply Now</span></td></tr>
      <tr><td class="col-title"><a href="#">Maecenas sed nibh</a></td><td class="col-date">Apr 8, 2015</td><td class="col-provider">Company Name</td><td><span class="apply">Apply Now</span></td></tr>
      <tr><td class="col-title"><a href="#">Maecenas sed nibh</a></td><td class="col-date">Apr 8, 2015</td><td class="col-provider">Company Name</td><td><span class="apply">Apply Now</span></td></tr>
      <tr><td class="col-title"><a href="#">Maecenas sed nibh</a></td><td class="col-date">Apr 8, 2015</td><td class="col-provider">Company Name</td><td><span class="apply">Apply Now</span></td></tr>
      <tr><td class="col-title"><a href="#">Maecenas sed nibh</a></td><td class="col-date">Apr 8, 2015</td><td class="col-provider">Company Name</td><td><span class="apply">Apply Now</span></td></tr>
      <tr><td class="col-title"><a href="#">Maecenas sed nibh</a></td><td class="col-date">Apr 8, 2015</td><td class="col-provider">Company Name</td><td><span class="apply">Apply Now</span></td></tr>
      <tr><td class="col-title"><a href="#">Maecenas sed nibh</a></td><td class="col-date">Apr 8, 2015</td><td class="col-provider">Company Name</td><td><span class="apply">Apply Now</span></td></tr>
      <tr><td class="col-title"><a href="#">Maecenas sed nibh</a></td><td class="col-date">Apr 8, 2015</td><td class="col-provider">Company Name</td><td><span class="apply">Apply Now</span></td></tr>
      <tr><td class="col-title"><a href="#">Maecenas sed nibh</a></td><td class="col-date">Apr 8, 2015</td><td class="col-provider">Company Name</td><td><span class="apply">Apply Now</span></td></tr>
      <tr><td class="col-title"><a href="#">Maecenas sed nibh</a></td><td class="col-date">Apr 8, 2015</td><td class="col-provider">Company Name</td><td><span class="apply">Apply Now</span></td></tr>
      <tr><td class="col-title"><a href="#">Maecenas sed nibh</a></td><td class="col-date">Apr 8, 2015</td><td class="col-provider">Company Name</td><td><span class="apply">Apply Now</span></td></tr>
      <tr><td class="col-title"><a href="#">Maecenas sed nibh</a></td><td class="col-date">Apr 8, 2015</td><td class="col-provider">Company Name</td><td><span class="apply">Apply Now</span></td></tr>
    </tbody>
  </table>
</main>

<section class="providers">
  <h2>Featured Job Providers</h2>
  <div class="carousel-arrows">
    <svg width="8" height="12" viewBox="0 0 8 12"><path d="M6 1 L1 6 L6 11" fill="none" stroke="#888" stroke-width="1.5"/></svg>
    <svg width="8" height="12" viewBox="0 0 8 12"><path d="M2 1 L7 6 L2 11" fill="none" stroke="#888" stroke-width="1.5"/></svg>
  </div>
  <ul class="provider-list">
    <li>Greenvale</li><li>Lumora</li><li>Tessaro</li><li>Orbisa</li><li>Pelmont</li><li>Doravel</li><li>Norvane</li><li>Quintel</li><li>Halvern</li>
  </ul>
</section>

<footer class="site-footer">
  <div class="footer-col" style="left:92px"><h3>QUICK LINKS</h3>
    <ul><li>Home</li><li>About Us</li><li>What We Do</li><li>Contact Us</li><li>Testimonials</li></ul></div>
  <div class="divider" style="left:198px"></div>
  <div class="footer-col" style="left:241px"><h3>OTHER LINKS</h3>
    <div class="cols2"><ul><li>Nunc sit amet</li><li>Proin a dolor</li><li>Phasellus</li><li>Aenean sed</li></ul>
    <ul><li>Praesent quis</li><li>Donec molestie</li><li>Donec molestiet</li><li>Vivamus gravida sem</li></ul></div></div>
  <div class="divider" style="left:521px"></div>
  <div class="footer-col" style="left:562px"><h3>MORE</h3>
    <div class="cols2"><ul><li>Nunc sit amet</li><li>Proin a dolor</li><li>Phasellus</li><li>Aenean sed</li></ul>
    <ul><li>Praesent quis</li><li>Donec molestie</li><li>Donec molestiet</li><li>Vivamus gravida sem</li></ul></div></div>
  <div class="divider" style="left:826px"></div>
  <div class="footer-col" style="left:859px"><h3>NEWSLETTER</h3>
    <div class="newsletter-field"><span>E-mail</span><b><svg width="12" height="14" viewBox="0 0 12 14"><path d="M1 1 L11 7 L1 13 Z" fill="#888"/></svg></b></div>
    <div class="social"><i style="background:#3b5998"></i><i style="background:#1da1f2"></i><i style="background:#0e76a8"></i></div>
  </div>
  <div class="rule"></div>
  <p class="copyright">Copyright&nbsp; © 2015&nbsp; Velundra Jobs.&nbsp;&nbsp; All rights reserved.</p>
  <div class="footer-icons">
    <svg width="26" height="26" viewBox="0 0 26 26"><circle cx="13" cy="13" r="12" fill="none" stroke="#ddd" stroke-width="1.5"/><rect x="7.5" y="9" width="11" height="8" fill="#ddd"/><path d="M7.5 9 L13 13.5 L18.5 9" fill="none" stroke="#333" stroke-width="1"/></svg>
    <svg width="26" height="26" viewBox="0 0 26 26"><circle cx="13" cy="13" r="12" fill="none" stroke="#999" stroke-width="1.5"/><path d="M13 19 V7 M8.5 11.5 L13 7 L17.5 11.5" fill="none" stroke="#999" stroke-width="1.8"/></svg>
  </div>
</footer>
</body>
</html>
```